Business Card Design & Gift cards, Gift Cert, Donation Card

Retail Gift Store-in addition to Business Cards we'd like sequenced 2 sided Gift cards, Gift Certificate Cards, and Donation Cards.please see examples and email for clarificationlogos attached with examples-
Gift Card, Gift Certificate and Donation Card will all be same style just differant upper right title, with back side info as example.
business card, as example is single sided.
looking for additional ideas for layout

Industry/Entity Type

Business

Contact Information for Business Card

211 Newman St.Pine Hollow, MI 48730989.362.8730Office@BrewKrew.com

Requirements
Must have
• Blue as per example
• Logos provided
• like gradiant background

```html
<!DOCTYPE html>
<html lang="en">
<head>
<meta charset="utf-8">
<title>Tillow Marsh – Business Card</title>
<link rel="stylesheet" href="https://fonts.googleapis.com/css2?family=Arimo:wght@400;700&display=swap">
<style>
  :root {
    --page: #eceef1;
    --sky-top: #9fcdef;
    --sky-bottom: #eef3f7;
    --band-blue: #3350a8;
    --swoosh-grey: #c4c8cc;
    --name-blue: #3d4fb0;
    --sun-yellow: #f4dc22;
    --text-white: #ffffff;
  }
  html, body {
    margin: 0;
    width: 1200px;
    height: 892px;
    overflow: hidden;
    background: var(--page);
    font-family: "Arimo", Arial, sans-serif;
  }
  .card {
    position: absolute;
    left: 280px;
    width: 640px;
    height: 366px;
    overflow: hidden;
    box-shadow: 0 6px 18px rgba(0,0,0,0.18);
  }
  .card--front {
    top: 44px;
    background: linear-gradient(200deg, var(--sky-top) 0%, var(--sky-bottom) 75%);
  }
  .card--back {
    top: 482px;
    background: linear-gradient(180deg, var(--sky-top) 0%, var(--sky-bottom) 85%);
  }
  .wave {
    position: absolute;
    inset: 0;
  }
  .brand {
    position: absolute;
    display: flex;
    align-items: center;
    gap: 12px;
    color: var(--name-blue);
    font-weight: 400;
    letter-spacing: 1px;
    text-transform: uppercase;
    white-space: nowrap;
  }
  .brand__dot {
    border-radius: 50%;
    background: var(--sun-yellow);
    flex: none;
  }
  .card--front .brand { left: 70px; top: 48px; font-size: 30px; }
  .card--front .brand__dot { width: 34px; height: 34px; }
  .card--back .brand {
    left: 0; right: 0; top: 150px;
    justify-content: center;
    font-size: 38px;
  }
  .card--back .brand__dot { width: 44px; height: 44px; }
  .contact {
    position: absolute;
    right: 22px;
    bottom: 24px;
    margin: 0;
    padding: 0;
    list-style: none;
    color: var(--text-white);
    font-size: 19px;
    font-weight: 400;
    text-align: right;
  }
  .contact__item {
    display: flex;
    justify-content: flex-end;
    align-items: center;
    gap: 14px;
    line-height: 28px;
    white-space: nowrap;
  }
  .contact__icon { width: 18px; height: 18px; flex: none; }
</style>
</head>
<body>

<section class="card card--front" aria-label="Business card front">
  <svg class="wave" viewBox="0 0 640 366" preserveAspectRatio="none" aria-hidden="true">
    <path d="M0,112 C190,128 330,220 640,222 L640,252 C330,254 190,150 0,132 Z" fill="var(--swoosh-grey)"/>
    <path d="M0,132 C190,150 330,254 640,252 L640,366 L0,366 Z" fill="var(--band-blue)"/>
  </svg>

  <div class="brand"><span class="brand__dot"></span><span class="brand__name">Tillow Marsh</span></div>

  <ul class="contact">
    <li class="contact__item">989.517.4296
      <svg class="contact__icon" viewBox="0 0 24 24"><path fill="var(--sun-yellow)" d="M6.6 10.8a15 15 0 0 0 6.6 6.6l2.2-2.2c.3-.3.7-.4 1-.2 1.1.4 2.3.6 3.6.6.6 0 1 .4 1 1V20c0 .6-.4 1-1 1A17 17 0 0 1 3 4c0-.6.4-1 1-1h3.5c.6 0 1 .4 1 1 0 1.3.2 2.5.6 3.6.1.3 0 .7-.2 1z"/></svg>
    </li>
    <li class="contact__item">Office@TillowMarsh.com
      <svg class="contact__icon" viewBox="0 0 24 24"><rect x="2" y="5" width="20" height="14" rx="1" fill="var(--sun-yellow)"/><path d="M2 6l10 7 10-7" fill="none" stroke="var(--band-blue)" stroke-width="1.6"/></svg>
    </li>
    <li class="contact__item">482 Larkfield Ave. Pine Hollow, OR 97362
      <svg class="contact__icon" viewBox="0 0 24 24"><path fill="var(--sun-yellow)" d="M12 2a7 7 0 0 0-7 7c0 5 7 13 7 13s7-8 7-13a7 7 0 0 0-7-7zm0 9.5A2.5 2.5 0 1 1 12 6.5a2.5 2.5 0 0 1 0 5z"/></svg>
    </li>
  </ul>
</section>

<section class="card card--back" aria-label="Business card back">
  <div class="brand"><span class="brand__dot"></span><span class="brand__name">Tillow Marsh</span></div>
</section>

</body>
</html>
```